Creative Web design for Tattoo Artist

I am a tattoo artist with a private tattoo/art studio in Cedar Hollow. I need to design a website for my studio, to include the following "pages" :
-home/about
-FAQ
-Gallery
-Inquiries
-shop
We would like to see designs that are more dark or "moody", and like the colors black/gold.
I'd like my website to reflect my studio, an award winning private, upscale custom only tattoo studio.

I've attached some examples of styles we liked.

Target Market(s)

adults ages 18-50, interested in tattoos, or fine art

Industry/Entity Type

Tattoos/Fine Art/Arts

Coding

Coded - Design and coding required

Number of Pages Required

5+ page

Colors

Designer to choose colors to be used in the design.

Requirements
Must have
• gallery section, and e-commerce page set up so I can begin selling merchandise, I'd like the fonts to flow with my logo design

```html
<!DOCTYPE html>
<html lang="en">
<head>
<meta charset="utf-8">
<title>Vesper Ink — Expert Tattoo &amp; Art Studio</title>
<link rel="stylesheet" href="https://fonts.googleapis.com/css2?family=Roboto+Condensed:wght@400;700;800&family=Roboto+Mono:wght@400;500&display=swap">
<style>
:root{
  --black:#070707;
  --ink:#0f0f0f;
  --panel:#161616;
  --band:#1c1c1c;
  --line:#2c2c2c;
  --gold:#d9a81e;
  --gold-soft:#b88d15;
  --white:#f4f4f4;
  --muted:#bdbdbd;
  --head:"Roboto Condensed", Arial, sans-serif;
  --mono:"Roboto Mono", "Courier New", monospace;
}
*{box-sizing:border-box;margin:0;padding:0}
html,body{width:1200px;height:4472px;overflow:hidden;background:var(--black);color:var(--white);font-family:var(--head)}
.page{position:relative;width:1200px;height:4472px;overflow:hidden}
.photo{position:absolute}

/* hero */
.hero{position:absolute;left:0;top:0;width:1200px;height:500px;background:radial-gradient(ellipse at 70% 35%,#3a3a3a 0%,#1c1c1c 40%,#080808 85%)}
.hero-ghost{position:absolute;left:96px;font:800 150px/1 var(--head);color:transparent;-webkit-text-stroke:2px rgba(255,255,255,.22);letter-spacing:2px;text-transform:uppercase;white-space:nowrap}
.hero-title{position:absolute;left:160px;font:700 64px/1 var(--head);text-transform:uppercase;color:var(--white);white-space:nowrap}
.hero-title .amp{color:var(--gold)}
.book-link{position:absolute;left:520px;top:424px;font:500 16px/1 var(--head);color:var(--gold);letter-spacing:1px;text-transform:uppercase;text-decoration:none}
.menu-icon{position:absolute;right:44px;top:28px;width:26px}
.menu-icon span{display:block;height:3px;background:var(--white);margin-bottom:5px}
.side-rail{position:absolute;right:40px;top:100px;width:28px;display:flex;flex-direction:column;align-items:center;gap:18px}
.side-rail .dot{width:12px;height:12px;border:2px solid var(--white);border-radius:50%}
.side-rail .rule{width:2px;height:90px;background:var(--white)}
.side-rail .vtext{writing-mode:vertical-rl;transform:rotate(180deg);font:700 13px/1 var(--head);letter-spacing:2px}

/* about */
.about-frame{position:absolute;left:172px;top:540px;width:328px;height:360px;border:3px solid var(--gold)}
.about-photo{left:100px;top:578px;width:380px;height:400px;background:linear-gradient(135deg,#4a4a4a,#1d1d1d 70%)}
.about-ghost{position:absolute;left:636px;top:566px;font:800 96px/1 var(--head);color:transparent;-webkit-text-stroke:2px rgba(255,255,255,.25);text-transform:uppercase;white-space:nowrap}
.about-title{position:absolute;left:640px;top:660px;font:700 50px/1.05 var(--head);color:var(--gold);text-transform:uppercase}
.about-text{position:absolute;left:640px;top:856px;width:460px;font:400 14px/1.55 var(--mono);color:var(--muted)}

/* browse */
.browse{position:absolute;left:0;top:1076px;width:1200px;height:200px;background:var(--band)}
.browse-title{position:absolute;left:200px;top:52px;font:700 32px/1 var(--head);color:var(--gold);text-transform:uppercase}
.browse-search{position:absolute;left:200px;top:96px;font:400 30px/1 var(--mono);color:#6c6c6c}
.browse-divider{position:absolute;left:732px;top:44px;width:2px;height:110px;background:#555}
.popular-title{position:absolute;left:772px;top:52px;font:400 24px/1 var(--mono)}
.tags{position:absolute;left:772px;top:96px;width:380px;display:flex;flex-wrap:wrap;gap:12px 10px}
.tag{font:400 12px/1 var(--mono);padding:6px 10px;background:#0c0c0c;color:var(--white)}
.tag.is-active{background:var(--gold);color:var(--black)}

/* headings */
.section-title{position:absolute;left:0;width:1200px;text-align:center;font:700 44px/1 var(--head);color:var(--gold);text-transform:uppercase}

/* shop */
.shop-band{position:absolute;left:0;top:1276px;width:1200px;height:560px;background:linear-gradient(#121212,#0a0a0a)}
.product{position:absolute;top:1428px;width:224px;height:320px;background:var(--panel);text-align:center}
.product .art{position:absolute;left:32px;top:24px;width:160px;height:170px;background:radial-gradient(circle,#3a2f10,#161616 70%)}
.product .art.shirt{background:radial-gradient(circle,#e8e8e8 0%,#9a9a9a 55%,#161616 72%)}
.product .name{position:absolute;left:0;top:206px;width:100%;font:700 26px/1 var(--head)}
.product .price{position:absolute;left:0;top:240px;width:100%;font:400 16px/1 var(--head);color:var(--muted)}
.product .cart{position:absolute;left:62px;top:266px;width:100px;height:26px;border-radius:6px;background:var(--gold);color:var(--black);font:700 13px/26px var(--head)}

/* faq */
.faq-photo{left:640px;top:2008px;width:452px;height:504px;background:linear-gradient(160deg,#3b3b3b,#121212 75%)}
.faq-panel{position:absolute;left:108px;top:2008px;width:532px;height:504px;background:var(--ink)}
.faq-open{position:absolute;left:134px;top:2056px;width:500px;height:136px;border:2px solid var(--gold);background:#0a0a0a}
.faq-open .q{position:relative;height:40px;background:var(--gold);color:var(--black);font:500 15px/40px var(--head);padding-left:20px}
.faq-open .a{padding:14px 20px;font:400 13px/1.5 var(--mono);color:var(--muted)}
.faq-item{position:absolute;left:154px;width:460px;font:500 16px/1 var(--head)}
.chev{position:absolute;right:0;top:-4px;width:24px;height:24px;border-radius:50%;background:var(--gold)}
.chev svg{position:absolute;left:6px;top:6px}
.faq-open .chev{right:14px;top:8px;background:var(--black)}

/* gallery */
.gallery{position:absolute;left:0;top:2668px;width:1200px;height:664px}

/* contact */
.map{left:108px;top:3508px;width:480px;height:384px;border-radius:40px;background:linear-gradient(135deg,#d9d9d9,#a9a9a9)}
.field{position:absolute;height:50px;background:var(--panel);font:400 15px/50px var(--head);color:var(--muted);padding-left:16px}
.field.msg{height:150px;line-height:1;padding-top:18px}
.submit{position:absolute;left:600px;top:3846px;width:104px;height:42px;border-radius:8px;background:var(--gold);color:var(--black);font:700 16px/42px var(--head);text-align:center}

/* cta */
.cta{position:absolute;left:100px;top:3988px;width:1000px;height:220px;border-radius:28px;background:var(--gold);text-align:center;color:var(--black)}
.cta h2{margin-top:36px;font:700 44px/1 var(--head);text-transform:uppercase}
.cta p{width:820px;margin:14px auto 0;font:400 15px/1.45 var(--mono)}
.cta .btn{display:inline-block;margin-top:14px;padding:0 22px;height:40px;border-radius:8px;background:var(--black);color:var(--white);font:700 16px/40px var(--head)}

/* footer */
.footer-brand{position:absolute;left:108px;top:4280px;display:flex;align-items:center;gap:10px;font:700 24px/1 var(--head);color:var(--gold)}
.footer-brand .mark{width:18px;height:18px;background:var(--gold)}
.footer-nav{position:absolute;left:268px;top:4284px;display:flex;font:400 16px/1 var(--head)}
.footer-nav span{padding:0 30px;border-right:1px solid #777}
.footer-nav span:first-child{padding-left:0}
.footer-nav span:last-child{border-right:0}
.footer-contact{position:absolute;left:268px;top:4344px;width:800px;display:flex;justify-content:space-between;font:400 14px/1 var(--head)}
.footer-contact .item{display:flex;align-items:center;gap:8px;white-space:nowrap}
.footer-contact .ic{width:20px;height:20px;border-radius:50%;background:var(--gold);display:flex;align-items:center;justify-content:center}
.footer-rule{position:absolute;left:268px;top:4384px;width:830px;height:1px;background:#444}
.copyright{position:absolute;left:268px;top:4400px;width:830px;text-align:center;font:400 11px/1 var(--head);color:var(--muted);letter-spacing:1px}
</style>
</head>
<body>
<div class="page">

  <!-- hero -->
  <section class="hero">
    <div class="photo" role="img" aria-label="Tattoo artist at work in a dim studio" style="left:0;top:0;width:1200px;height:500px;background:radial-gradient(ellipse at 68% 30%,rgba(90,90,90,.55),rgba(0,0,0,0) 55%)"></div>
    <div class="hero-ghost" style="top:112px">Tattoo</div>
    <div class="hero-ghost" style="top:232px;left:120px">Art Studio</div>
    <h1 class="hero-title" style="top:150px">Expert Tattoo</h1>
    <div class="hero-title" style="top:256px;left:272px;font-size:54px"><span class="amp">&amp;</span> Art Studio</div>
    <a class="book-link">Book your appointment →</a>
    <div class="menu-icon"><span></span><span></span><span></span></div>
    <div class="side-rail">
      <div class="dot"></div><div class="dot"></div><div class="dot"></div><div class="dot"></div>
      <div class="rule"></div>
      <div class="vtext">BOOK NOW</div>
    </div>
  </section>

  <!-- about -->
  <section>
    <div class="about-frame"></div>
    <div class="photo about-photo" role="img" aria-label="Portrait of the tattoo artist in the studio"></div>
    <div class="about-ghost">About VIS</div>
    <h2 class="about-title">Express<br>yourself with<br>tattoo art</h2>
    <p class="about-text">Lorem ipsum dolor sit amet, consectetur adipiscing elit, sed do eiusmod tempor incididunt ut labore et dolore magna aliqua. Ut enim ad minim veniam, quis nostrud exercitation ullamco laboris nisi ut aliquip ex ea commodo consequat. Duis aute irure dolor in reprehenderit in voluptate velit esse cillum dolore eu fugiat nulla pariatur.</p>
  </section>

  <!-- browse -->
  <section class="browse">
    <h2 class="browse-title">Browse Tattoo Art Designs</h2>
    <div class="browse-search">Search Here...</div>
    <div class="browse-divider"></div>
    <div class="popular-title">Popular Search</div>
    <div class="tags">
      <span class="tag">Fine Work</span>
      <span class="tag is-active">Black and Grey</span>
      <span class="tag">Blood &amp; Gray</span>
      <span class="tag">Script</span>
      <span class="tag">Realism</span>
    </div>
  </section>

  <!-- shop -->
  <div class="shop-band"></div>
  <h2 class="section-title" style="top:1320px">Shop</h2>
  <div class="product" style="left:108px"><div class="art shirt" role="img" aria-label="Grey studio t-shirt"></div><div class="name">T-shirts</div><div class="price">$35.00</div><div class="cart">Add To Cart</div></div>
  <div class="product" style="left:360px"><div class="art" role="img" aria-label="Gold dragon tattoo design"></div><div class="name">Lorem ipsum</div><div class="price">$260.00</div><div class="cart">Add To Cart</div></div>
  <div class="product" style="left:612px"><div class="art" role="img" aria-label="Gold tiger tattoo design"></div><div class="name">Lorem ipsum</div><div class="price">$35.00</div><div class="cart">Add To Cart</div></div>
  <div class="product" style="left:864px"><div class="art" role="img" aria-label="Gold phoenix tattoo design"></div><div class="name">Lorem ipsum</div><div class="price">$25.00</div><div class="cart">Add To Cart</div></div>

  <!-- faq -->
  <h2 class="section-title" style="top:1922px">Frequently Asked Questions</h2>
  <div class="faq-panel"></div>
  <div class="photo faq-photo" role="img" aria-label="Close-up of a tattoo being inked"></div>
  <div class="faq-open">
    <div class="q">Lorem ipsum dolor sit amet, consectetur
      <span class="chev"><svg width="12" height="12" viewBox="0 0 12 12"><path d="M2 8l4-4 4 4" stroke="#d9a81e" stroke-width="2" fill="none"/></svg></span></div>
    <div class="a">Lorem ipsum dolor sit amet, consectetur adipiscing elit, sed do eiusmod tempor incididunt ut labore et dolore magna aliqua.enim ad minim veniam, quis nostrud.</div>
  </div>
  <div class="faq-item" style="top:2222px">Lorem ipsum dolor sit amet, consectetur<span class="chev"><svg width="12" height="12" viewBox="0 0 12 12"><path d="M2 4l4 4 4-4" stroke="#070707" stroke-width="2" fill="none"/></svg></span></div>
  <div class="faq-item" style="top:2278px">Lorem ipsum dolor sit amet, consectetur<span class="chev"><svg width="12" height="12" viewBox="0 0 12 12"><path d="M2 4l4 4 4-4" stroke="#070707" stroke-width="2" fill="none"/></svg></span></div>
  <div class="faq-item" style="top:2334px">Lorem ipsum dolor sit amet, consectetur<span class="chev"><svg width="12" height="12" viewBox="0 0 12 12"><path d="M2 4l4 4 4-4" stroke="#070707" stroke-width="2" fill="none"/></svg></span></div>
  <div class="faq-item" style="top:2384px">Lorem ipsum dolor sit amet, consectetur<span class="chev"><svg width="12" height="12" viewBox="0 0 12 12"><path d="M2 4l4 4 4-4" stroke="#070707" stroke-width="2" fill="none"/></svg></span></div>
  <div class="faq-item" style="top:2434px">Lorem ipsum dolor sit amet, consectetur<span class="chev"><svg width="12" height="12" viewBox="0 0 12 12"><path d="M2 4l4 4 4-4" stroke="#070707" stroke-width="2" fill="none"/></svg></span></div>

  <!-- gallery -->
  <h2 class="section-title" style="top:2570px">Gallery</h2>
  <div class="gallery">
    <div class="photo" role="img" aria-label="Tattooed man portrait" style="left:0;top:0;width:296px;height:452px;background:linear-gradient(160deg,#5a5a5a,#1a1a1a)"></div>
    <div class="photo" role="img" aria-label="Tattoo artist working on a client" style="left:300px;top:0;width:296px;height:210px;background:linear-gradient(135deg,#2e2e2e,#0f0f0f)"></div>
    <div class="photo" role="img" aria-label="Tattooed arms close-up" style="left:600px;top:0;width:300px;height:210px;background:linear-gradient(135deg,#6a6a6a,#2a2a2a)"></div>
    <div class="photo" role="img" aria-label="Woman with tattooed shoulder" style="left:904px;top:0;width:296px;height:210px;background:linear-gradient(135deg,#8a8a8a,#303030)"></div>
    <div class="photo" role="img" aria-label="Artist inking a tattoo" style="left:300px;top:214px;width:180px;height:238px;background:linear-gradient(135deg,#3a3a3a,#121212)"></div>
    <div class="photo" role="img" aria-label="Artist working at the studio bench" style="left:484px;top:214px;width:416px;height:238px;background:linear-gradient(135deg,#505050,#1a1a1a)"></div>
    <div class="photo" role="img" aria-label="Tattooed back" style="left:904px;top:214px;width:296px;height:238px;background:linear-gradient(135deg,#4a4a4a,#161616)"></div>
    <div class="photo" role="img" aria-label="Tattoo machine in hand" style="left:0;top:456px;width:296px;height:208px;background:linear-gradient(135deg,#6e6e6e,#1a1a1a)"></div>
    <div class="photo" role="img" aria-label="Client smiling in the studio" style="left:300px;top:456px;width:296px;height:208px;background:linear-gradient(135deg,#5e5e5e,#202020)"></div>
    <div class="photo" role="img" aria-label="Fresh tattoo being finished" style="left:600px;top:456px;width:300px;height:208px;background:linear-gradient(135deg,#3e3e3e,#121212)"></div>
    <div class="photo" role="img" aria-label="Studio detail shot" style="left:904px;top:456px;width:296px;height:208px;background:#070707"></div>
  </div>

  <!-- contact -->
  <h2 class="section-title" style="top:3420px">Contact Us</h2>
  <div class="photo map" role="img" aria-label="Street map around the studio"></div>
  <div class="field" style="left:600px;top:3536px;width:492px">Name</div>
  <div class="field" style="left:600px;top:3600px;width:240px">Phone Number</div>
  <div class="field" style="left:852px;top:3600px;width:240px">Phone Number</div>
  <div class="field msg" style="left:600px;top:3664px;width:492px">Message</div>
  <div class="submit">SUBMIT</div>

  <!-- cta -->
  <section class="cta">
    <h2>Ready to custom tattoo</h2>
    <p>Lorem ipsum dolor sit amet, consectetur adipiscing elit, sed do eiusmod tempor incididunt ut labore et dolore magna aliqua. Ut enim ad minim veniam, quis nostrud exercitation ullamco laboris nisi.</p>
    <span class="btn">Contact Us Today!</span>
  </section>

  <!-- footer -->
  <footer>
    <div class="footer-brand"><span class="mark"></span>Vesper Ink</div>
    <nav class="footer-nav"><span>Home</span><span>About</span><span>FAQ</span><span>Gallery</span><span>Inquiries</span><span>Shop</span></nav>
    <div class="footer-contact">
      <div class="item"><span class="ic"><svg width="10" height="12" viewBox="0 0 10 12"><path d="M5 0a4 4 0 0 0-4 4c0 3 4 8 4 8s4-5 4-8a4 4 0 0 0-4-4z" fill="#070707"/></svg></span>55 Lorem Ipsum Dolor Cedar Hollow</div>
      <div class="item"><span class="ic"><svg width="12" height="9" viewBox="0 0 12 9"><rect x="0.5" y="0.5" width="11" height="8" fill="none" stroke="#070707"/><path d="M0.5 0.5l5.5 4 5.5-4" fill="none" stroke="#070707"/></svg></span>hello@vesperinkstudio.com</div>
      <div class="item"><span class="ic"><svg width="10" height="10" viewBox="0 0 10 10"><path d="M2 0l2 2.5-1 1.2a6 6 0 0 0 3.3 3.3l1.2-1L10 8l-1.5 2C4 10 0 6 0 1.5z" fill="#070707"/></svg></span>+1 000 000 0000</div>
    </div>
    <div class="footer-rule"></div>
    <div class="copyright">COPYRIGHT © 2024 VESPERINKSTUDIO | ALL RIGHTS RESERVED</div>
  </footer>

</div>
</body>
</html>
```